HotSite for a 3-day Conference (To build in 24hs)

We need a hot-site for our 3-Day Conference before next Wednesday 17/Jan.

How is it now:
Today all information about our conference is shown in 1 simple page inside our website: https://www.kelvortaplin.com/grand-lodging-forum.

What we need:
A hot-site focused on our conference where people can see all information about the event, buy tickets and pay it on-line.

The visual:
Luxury, minimalist menu, big full screen light video backgrounds.

Index:
Full animated/light video image and:
Grand Lodging Forum® Paris - 2024
1, 2 and 3rd November
Hotel Le Moulin Doré
REGISTER NOW

MENU
I want a double layer/line top menu:

- First menu line (smaller, not the most important/relevant)
- Second menu line (main menu)

First menu line:
About us
Conferences
Newsroom
Careers
Become a Sponsor

The main menu items are:
AGENDA
SPEAKERS
SPONSORS
PREVIOUS EDITIONS
ATTEND/REGISTER NOW

Some references:
https://primeworld.live.qz.com
https://brevand.us/conference
https://www.holtrane.com/en/conferences

```html
<!DOCTYPE html>
<html lang="en">
<head>
<meta charset="utf-8">
<title>Grand Lodging Forum® Paris 2024</title>
<link href="https://fonts.googleapis.com/css2?family=Pinyon+Script&family=Poppins:wght@400;500&display=swap" rel="stylesheet">
<style>
:root{
  --gold:#cfb57b;
  --gold-card:#bfa979;
  --charcoal:#575759;
  --charcoal-dark:#4f4f51;
  --paper:#f4f4f4;
  --ink:#222;
  --text:#333;
  --white:#fff;
  --red:#d11f1f;
}
*{box-sizing:border-box;margin:0;padding:0}
html,body{width:1200px;height:2901px;overflow:hidden}
body{font-family:"Poppins",sans-serif;color:var(--text);background:var(--paper);position:relative}
.script{font-family:"Pinyon Script",cursive;font-weight:400}
section,header,footer{position:absolute;left:0;width:1200px}
.abs{position:absolute}

/* header */
.site-header{top:0;height:110px;background:var(--charcoal)}
.top-band{position:absolute;top:0;right:0;width:903px;height:47px}
.brand{position:absolute;left:113px;top:28px;display:flex;align-items:center;gap:8px;color:var(--gold);font-size:20px;font-weight:400;letter-spacing:.5px}
.brand-dot{width:12px;height:12px;border:1.5px solid var(--gold);border-radius:50%}
.top-nav{position:absolute;top:13px;right:111px;display:flex;gap:29px;font-size:14px;color:var(--white)}
.main-nav{position:absolute;top:65px;left:513px;display:flex;gap:25px;font-size:16px;color:var(--white)}
.btn-register{position:absolute;left:940px;top:60px;width:149px;height:36px;background:var(--gold);color:var(--white);font-size:15.5px;display:flex;align-items:center;justify-content:center}

/* hero */
.hero{top:110px;height:541px}
.hero-media{position:absolute;inset:0;background:linear-gradient(180deg,#3d3d3d 0%,#5a5a5a 45%,#6e6e6e 75%,#8a8a8a 100%)}
.hero-title{position:absolute;top:178px;width:100%;text-align:center;font-size:64px;color:var(--white)}
.play{position:absolute;left:570px;top:269px}

/* intro */
.intro{top:651px;height:631px;background:var(--paper)}
.heading{font-size:44px;color:var(--ink);line-height:1}
.rule{height:3px;background:var(--gold);width:108px;margin-top:12px}
.intro-copy{position:absolute;left:111px;top:150px;width:489px;font-size:14.7px;line-height:25px;text-align:justify;color:var(--text)}
.tick-list{list-style:none;font-size:14.7px;color:var(--text)}
.tick-list li{display:flex;align-items:flex-start;gap:8px}
.tick{flex:none;width:17px;height:17px;margin-top:3px}
.content-list li{height:30px}
.tuition-list li{margin-bottom:14px;line-height:22px}
.note-list{list-style:none;font-size:14.7px}
.note-list li{display:flex;align-items:center;gap:7px;height:32px}

/* speakers */
.speakers{top:1282px;height:658px;background:var(--charcoal)}
.section-title{position:absolute;width:100%;text-align:center;font-size:44px}
.title-rule{position:absolute;left:546px;width:108px;height:3px;background:var(--gold)}
.speaker{position:absolute;top:184px;width:184px;text-align:center;color:var(--white)}
.speaker-photo{width:184px;height:207px;background:linear-gradient(160deg,#6a6f6c,#2f3236)}
.speaker-name{font-size:25px;margin-top:22px;line-height:1.1}
.speaker-role{font-size:15.5px;line-height:22px;margin-top:2px;margin-left:-30px;margin-right:-30px}
.arrow{position:absolute;top:1804px}

/* schedule */
.schedule{top:1940px;height:735px;background:var(--paper)}
.day-card{position:absolute;top:183px;width:318px;padding:18px 12px;border-radius:14px;color:var(--white);font-size:12.6px;line-height:21px;box-shadow:0 3px 8px rgba(0,0,0,.15)}
.day-card.gold{background:var(--gold-card);height:395px}
.day-card.dark{background:var(--charcoal);height:466px}
.day-title{font-size:23px;margin-bottom:12px;line-height:1.3}
.slot{margin-bottom:9px}

/* footer */
.site-footer{top:2675px;height:226px;background:var(--charcoal);color:var(--white)}
.footer-brand{position:absolute;top:62px;width:100%;display:flex;justify-content:center;align-items:center;gap:8px;color:var(--gold);font-size:20px}
.footer-nav{position:absolute;top:119px;width:100%;display:flex;justify-content:center;gap:25px;font-size:16px}
.copyright{position:absolute;top:188px;width:100%;text-align:center;font-size:15.5px}
</style>
</head>
<body>

<header class="site-header">
  <svg class="top-band" viewBox="0 0 903 47" aria-hidden="true"><polygon points="0,0 903,0 903,47 45,47" fill="#cfb57b"/></svg>
  <div class="brand"><span class="brand-dot"></span>Kelvor Taplin</div>
  <nav class="top-nav"><span>About us</span><span>Conferences</span><span>Newsroom</span><span>Careers</span><span>Become a Sponsor</span></nav>
  <nav class="main-nav"><span>Agenda</span><span>Speakers</span><span>Sponsors</span><span>Previous Editions</span></nav>
  <div class="btn-register">Register Now</div>
</header>

<section class="hero">
  <div class="hero-media" role="img" aria-label="Black and white photo of a classical Parisian palace facade with arched windows and a paved courtyard"></div>
  <h1 class="hero-title script">Grand Lodging Forum</h1>
  <svg class="play" width="60" height="60" viewBox="0 0 60 60" aria-label="Play video" role="img"><circle cx="30" cy="30" r="30" fill="#cfb57b"/><polygon points="23,18 43,30 23,42" fill="#333"/></svg>
</section>

<section class="intro">
  <div class="abs" style="left:111px;top:82px">
    <h2 class="heading script">Paris <span style="font-size:44px">–</span> <span style="font-size:28px">November 1-3, 2024</span></h2>
    <div class="rule"></div>
  </div>
  <p class="intro-copy">The ever-growing Luxury Hospitality business is one of the most exciting industries in the world. At our Grand Lodging Forum, top figures in the industry share their experiences and give unique insights, speaking about challenges, entrepreneurial management, vision and prospects for the future. The forum leads directly into Hotelia Expo, the most important Hospitality event in the world.</p>

  <div class="abs" style="left:111px;top:325px">
    <h2 class="heading script">Tuition</h2>
    <div class="rule"></div>
  </div>
  <ul class="tick-list tuition-list abs" style="left:111px;top:395px">
    <li><svg class="tick" viewBox="0 0 17 17"><circle cx="8.5" cy="8.5" r="8.5" fill="#cfb57b"/><path d="M4.5 8.8l2.7 2.6 5.3-5.5" stroke="#fff" stroke-width="1.8" fill="none"/></svg><span>Early birds - until 08/30/2024&nbsp; €3.750,00</span></li>
    <li><svg class="tick" viewBox="0 0 17 17"><circle cx="8.5" cy="8.5" r="8.5" fill="#cfb57b"/><path d="M4.5 8.8l2.7 2.6 5.3-5.5" stroke="#fff" stroke-width="1.8" fill="none"/></svg><span>After 08/30/2024&nbsp; €5.000,00</span></li>
    <li><svg class="tick" viewBox="0 0 17 17"><circle cx="8.5" cy="8.5" r="8.5" fill="#cfb57b"/><path d="M4.5 8.8l2.7 2.6 5.3-5.5" stroke="#fff" stroke-width="1.8" fill="none"/></svg><span>Kelvor Taplin Students<br>Early birds - until 08/30/2024 €3.000,00</span></li>
    <li><svg class="tick" viewBox="0 0 17 17"><circle cx="8.5" cy="8.5" r="8.5" fill="#cfb57b"/><path d="M4.5 8.8l2.7 2.6 5.3-5.5" stroke="#fff" stroke-width="1.8" fill="none"/></svg><span>After 08/30/2024 €3.500,00</span></li>
  </ul>

  <div class="abs" style="left:710px;top:82px">
    <h2 class="heading script">Content</h2>
    <div class="rule"></div>
  </div>
  <ul class="tick-list content-list abs" style="left:709px;top:154px">
    <li><svg class="tick" viewBox="0 0 17 17"><circle cx="8.5" cy="8.5" r="8.5" fill="#cfb57b"/><path d="M4.5 8.8l2.7 2.6 5.3-5.5" stroke="#fff" stroke-width="1.8" fill="none"/></svg>The Luxury Traveller’s Evolution Over Time</li>
    <li><svg class="tick" viewBox="0 0 17 17"><circle cx="8.5" cy="8.5" r="8.5" fill="#cfb57b"/><path d="M4.5 8.8l2.7 2.6 5.3-5.5" stroke="#fff" stroke-width="1.8" fill="none"/></svg>Luxury Consumer Behavior</li>
    <li><svg class="tick" viewBox="0 0 17 17"><circle cx="8.5" cy="8.5" r="8.5" fill="#cfb57b"/><path d="M4.5 8.8l2.7 2.6 5.3-5.5" stroke="#fff" stroke-width="1.8" fill="none"/></svg>New Distribution Channels in Luxury Hospitality</li>
    <li><svg class="tick" viewBox="0 0 17 17"><circle cx="8.5" cy="8.5" r="8.5" fill="#cfb57b"/><path d="M4.5 8.8l2.7 2.6 5.3-5.5" stroke="#fff" stroke-width="1.8" fill="none"/></svg>Luxury Brand Management</li>
    <li><svg class="tick" viewBox="0 0 17 17"><circle cx="8.5" cy="8.5" r="8.5" fill="#cfb57b"/><path d="M4.5 8.8l2.7 2.6 5.3-5.5" stroke="#fff" stroke-width="1.8" fill="none"/></svg>Innovation in Luxury Hospitality</li>
    <li><svg class="tick" viewBox="0 0 17 17"><circle cx="8.5" cy="8.5" r="8.5" fill="#cfb57b"/><path d="M4.5 8.8l2.7 2.6 5.3-5.5" stroke="#fff" stroke-width="1.8" fill="none"/></svg>Luxury Boutique Hotel Strategies</li>
    <li><svg class="tick" viewBox="0 0 17 17"><circle cx="8.5" cy="8.5" r="8.5" fill="#cfb57b"/><path d="M4.5 8.8l2.7 2.6 5.3-5.5" stroke="#fff" stroke-width="1.8" fill="none"/></svg>How to Maintain Luxury in Large Scale Operations</li>
    <li><svg class="tick" viewBox="0 0 17 17"><circle cx="8.5" cy="8.5" r="8.5" fill="#cfb57b"/><path d="M4.5 8.8l2.7 2.6 5.3-5.5" stroke="#fff" stroke-width="1.8" fill="none"/></svg>Generating Unique Experiences</li>
    <li><svg class="tick" viewBox="0 0 17 17"><circle cx="8.5" cy="8.5" r="8.5" fill="#cfb57b"/><path d="M4.5 8.8l2.7 2.6 5.3-5.5" stroke="#fff" stroke-width="1.8" fill="none"/></svg>Luxury Hotel Chain Management</li>
    <li><svg class="tick" viewBox="0 0 17 17"><circle cx="8.5" cy="8.5" r="8.5" fill="#cfb57b"/><path d="M4.5 8.8l2.7 2.6 5.3-5.5" stroke="#fff" stroke-width="1.8" fill="none"/></svg>Forming Strategic Alliances</li>
  </ul>
  <ul class="note-list abs" style="left:667px;top:479px">
    <li><svg width="18" height="18" viewBox="0 0 18 18"><polygon points="9,0 11,5 16,3 13,8 18,9 13,11 16,15 11,13 9,18 7,13 2,15 5,11 0,9 5,8 2,3 7,5" fill="#d11f1f"/></svg>Discounts available for groups and partner Universities</li>
    <li><svg width="18" height="18" viewBox="0 0 18 18"><polygon points="9,0 11,5 16,3 13,8 18,9 13,11 16,15 11,13 9,18 7,13 2,15 5,11 0,9 5,8 2,3 7,5" fill="#d11f1f"/></svg>Lodgind and meals not included</li>
  </ul>
</section>

<section class="speakers">
  <h2 class="section-title script" style="top:70px;color:#fff">Speaker Line-Up</h2>
  <div class="title-rule" style="top:132px"></div>
  <div class="speaker" style="left:172px"><div class="speaker-photo" role="img" aria-label="Portrait photo of Renato Valdera"></div><div class="speaker-name script">Renato Valdera</div><div class="speaker-role">President of Kelvor Taplin</div></div>
  <div class="speaker" style="left:397px"><div class="speaker-photo" role="img" aria-label="Portrait photo of Jean-Marc Doriel" style="background:linear-gradient(90deg,#2a2f3d 70%,#9b1d22)"></div><div class="speaker-name script">Jean-Marc Doriel</div><div class="speaker-role">CEO, La Clairière</div></div>
  <div class="speaker" style="left:621px"><div class="speaker-photo" role="img" aria-label="Portrait photo of Christoph Balder" style="background:linear-gradient(160deg,#4f7a3e,#2c3a4a)"></div><div class="speaker-name script">Christoph Balder</div><div class="speaker-role">General Director,<br>Hotel Astoria Paris</div></div>
  <div class="speaker" style="left:846px"><div class="speaker-photo" role="img" aria-label="Portrait photo of Luca Verrano" style="background:linear-gradient(160deg,#e9e9ec,#27355a)"></div><div class="speaker-name script">Luca Verrano</div><div class="speaker-role">Former VP,<br>Cedar Crest Resorts</div></div>
  <svg class="abs" style="left:532px;top:522px" width="50" height="50" viewBox="0 0 50 50" role="img" aria-label="Previous"><circle cx="25" cy="25" r="25" fill="#fff"/><path d="M29 15l-10 10 10 10" stroke="#333" stroke-width="3.5" fill="none"/></svg>
  <svg class="abs" style="left:618px;top:522px" width="50" height="50" viewBox="0 0 50 50" role="img" aria-label="Next"><circle cx="25" cy="25" r="25" fill="#fff"/><path d="M21 15l10 10-10 10" stroke="#333" stroke-width="3.5" fill="none"/></svg>
</section>

<section class="schedule">
  <h2 class="section-title script" style="top:77px;color:var(--ink)">Daily Schedule</h2>
  <div class="title-rule" style="top:141px"></div>

  <article class="day-card gold" style="left:111px">
    <h3 class="day-title script">Nov. 3 – A Glimpse of the Future</h3>
    <p class="slot">09:00 -&nbsp; Innovation in Luxury Hospitality<br>Luca Verrano | Nestwell</p>
    <p class="slot">10:30 - Coffee Break</p>
    <p class="slot">11:00 - Site Inspection - Hotel Plaza Verlaine</p>
    <p class="slot">12:00 - Lunch</p>
    <p class="slot">14:00 - Luxury Hotel Chain Management<br>François Delmont | Ashbury Collection</p>
    <p class="slot">15:30 - Coffee Break</p>
    <p class="slot">16:00 - Panel of Discussion - New Competitors</p>
    <p class="slot">17:00 - Closure and Certificates</p>
  </article>

  <article class="day-card dark" style="left:442px">
    <h3 class="day-title script">Nov. 2 – The Era of Experiences</h3>
    <p class="slot">09:00 - Luxury Boutique Hotel Strategies<br>Jean-Marc Doriel | La Clairière</p>
    <p class="slot">10:30 - Coffee Break</p>
    <p class="slot">11:00 - Generating Unique Experiences</p>
    <p class="slot">Jean-Marc Doriel | La Clairière</p>
    <p class="slot">12:00 - Lunch</p>
    <p class="slot">14:00 - Smaller is Greater<br>Filip Borwen | Select Boutique Hotels of the World</p>
    <p class="slot">15:30 - Coffee Break</p>
    <p class="slot">16:00 - Site Inspection - Spa Hotel La Clairière</p>
    <p class="slot">17:00 - Closure</p>
    <p class="slot">17:30 - Social Program - Guided Visit to Grand Musée</p>
  </article>

  <article class="day-card gold" style="left:772px">
    <h3 class="day-title script">Nov. 3 – A Glimpse of the Future</h3>
    <p class="slot">09:00 -&nbsp; Innovation in Luxury Hospitality<br>Luca Verrano | Nestwell</p>
    <p class="slot">10:30 - Coffee Break</p>
    <p class="slot">11:00 - Site Inspection - Hotel Plaza Verlaine</p>
    <p class="slot">12:00 - Lunch</p>
    <p class="slot">14:00 - Luxury Hotel Chain Management<br>François Delmont | Ashbury Collection</p>
    <p class="slot">15:30 - Coffee Break</p>
    <p class="slot">16:00 - Panel of Discussion - New Competitors</p>
    <p class="slot">17:00 - Closure and Certificates</p>
  </article>
</section>

<footer class="site-footer">
  <div class="footer-brand"><span class="brand-dot"></span>Kelvor Taplin</div>
  <nav class="footer-nav"><span>Agenda</span><span>Speakers</span><span>Sponsors</span><span>Previous Editions</span><span>Attend/register Now</span></nav>
  <p class="copyright">©2024 Kelvortaplin | All Rights Reserved.</p>
</footer>

</body>
</html>
```